Eyecatching Carpentry Business card

I need a business card designed for myself, my company name is Tom Hadley Carpentry.
I am based on the south coast of England and I do all aspects of carpentry, including;
skirting
Architraves
kitchens
roof construction
flooring
doors
loft conversions
decking
windows
I currently have no company logo or letter head so I leave all design ideas to designers.
All I ask is that it looks professional and modern.
A logo may be incorporated as well.
My contact details should be on the back, telephone and email.

```html
<!DOCTYPE html>
<html lang="en">
<head>
<meta charset="utf-8">
<title>Tom Hadley Carpentry – Business Card</title>
<link rel="stylesheet" href="https://fonts.googleapis.com/css2?family=Open+Sans:ital,wght@0,400;0,600;0,700;1,700&display=swap">
<style>
  :root {
    --backdrop: #d9d9d9;
    --card: #ffffff;
    --band-dark: #6e6e6e;
    --band-mid: #a5a5a5;
    --band-light: #efefef;
    --ink: #3a3a3a;
    --ink-soft: #5c5c5c;
    --accent: #8c1c1c;
    --rule: #cfcfcf;
  }
  * { box-sizing: border-box; margin: 0; padding: 0; }
  html, body { width: 1200px; height: 1005px; overflow: hidden; }
  body {
    background: var(--backdrop);
    font-family: "Open Sans", Arial, sans-serif;
    color: var(--ink);
    position: relative;
  }
  .card {
    position: absolute;
    left: 150px;
    width: 900px;
    height: 450px;
    background: var(--card);
    overflow: hidden;
    box-shadow: 0 2px 6px rgba(0,0,0,.12);
  }
  .card--front { top: 35px; }
  .card--back { top: 520px; }

  /* brand lockup */
  .brand {
    display: flex;
    align-items: center;
    gap: 16px;
  }
  .brand__mark {
    width: 38px; height: 38px;
    border: 3px solid var(--accent);
    border-radius: 6px;
  }
  .brand__name {
    font-weight: 400;
    font-size: 40px;
    color: var(--ink-soft);
    letter-spacing: .5px;
  }

  .card--front .brand {
    position: absolute;
    left: 0; right: 0; top: 170px;
    justify-content: center;
  }
  .front__web {
    position: absolute;
    left: 0; right: 0; top: 255px;
    text-align: center;
    font-size: 19px;
    color: var(--ink);
  }

  /* back side bands */
  .band {
    position: absolute;
    left: 0; right: 0;
  }
  .band--top { top: 60px; height: 12px; background: var(--band-dark); }
  .band--panel { top: 72px; height: 170px; left: 300px; background: var(--band-light); }
  .band--foot { top: 242px; height: 22px; left: 300px; background: var(--band-dark); }

  .name-tab {
    position: absolute;
    left: 0; top: 60px;
    width: 370px; height: 62px;
    background: var(--band-dark);
    clip-path: polygon(0 0, 100% 0, 91% 100%, 0 100%);
  }
  .name-tab__name {
    position: absolute;
    left: 30px; top: 13px;
    font-weight: 700;
    font-style: italic;
    font-size: 28px;
    color: #fff;
    letter-spacing: .5px;
    text-transform: uppercase;
  }
  .role {
    position: absolute;
    left: 385px; top: 96px;
    font-weight: 700;
    font-size: 19px;
    color: var(--accent);
  }

  .contacts {
    position: absolute;
    left: 22px; top: 140px;
    width: 300px;
    list-style: none;
  }
  .contacts__item {
    display: flex;
    align-items: flex-start;
    gap: 22px;
    padding: 10px 0 12px;
    border-bottom: 1px solid var(--rule);
    font-size: 18px;
    line-height: 1.3;
    color: var(--ink);
  }
  .contacts__item:last-child { border-bottom: none; }
  .contacts__icon { width: 26px; height: 26px; flex: none; fill: var(--accent); }

  .card--back .brand {
    position: absolute;
    right: 60px; bottom: 70px;
  }
</style>
</head>
<body>

  <section class="card card--front" aria-label="Card front">
    <div class="brand">
      <span class="brand__mark" aria-hidden="true"></span>
      <span class="brand__name">Tom Hadley Carpentry</span>
    </div>
    <p class="front__web">www.hadleycarpentry.co.uk</p>
  </section>

  <section class="card card--back" aria-label="Card back">
    <div class="band band--top"></div>
    <div class="band band--panel"></div>
    <div class="band band--foot"></div>

    <div class="name-tab"><span class="name-tab__name">Tom Hadley</span></div>
    <p class="role">Managing Director</p>

    <ul class="contacts">
      <li class="contacts__item">
        <svg class="contacts__icon" viewBox="0 0 24 24" aria-hidden="true"><path d="M12 2a7 7 0 0 0-7 7c0 5 7 13 7 13s7-8 7-13a7 7 0 0 0-7-7zm0 9.5A2.5 2.5 0 1 1 12 6.5a2.5 2.5 0 0 1 0 5z"/></svg>
        <span>12 Harbour Lane,<br>Southsea PO5 3AB</span>
      </li>
      <li class="contacts__item">
        <svg class="contacts__icon" viewBox="0 0 24 24" aria-hidden="true"><path d="M6.6 10.8a15 15 0 0 0 6.6 6.6l2.2-2.2a1 1 0 0 1 1-.25 11.4 11.4 0 0 0 3.6.57 1 1 0 0 1 1 1V20a1 1 0 0 1-1 1A17 17 0 0 1 3 4a1 1 0 0 1 1-1h3.5a1 1 0 0 1 1 1c0 1.25.2 2.45.57 3.57a1 1 0 0 1-.25 1z"/></svg>
        <span>01234 567 890<br>07700 900 123</span>
      </li>
      <li class="contacts__item">
        <svg class="contacts__icon" viewBox="0 0 24 24" aria-hidden="true"><path d="M2 5h20v14H2zm2 2v.5l8 5 8-5V7zm0 3v7h16v-7l-8 5z"/></svg>
        <span>hello@hadleycarpentry.co.uk</span>
      </li>
      <li class="contacts__item">
        <svg class="contacts__icon" viewBox="0 0 24 24" aria-hidden="true"><path d="M12 2a10 10 0 1 0 0 20 10 10 0 0 0 0-20zm6.9 6h-3a15 15 0 0 0-1.3-3.6A8 8 0 0 1 18.9 8zM12 4c.8 1.1 1.5 2.5 1.9 4h-3.8c.4-1.5 1.1-2.9 1.9-4zM4.3 14a8 8 0 0 1 0-4h3.4a16 16 0 0 0 0 4zm.8 2h3a15 15 0 0 0 1.3 3.6A8 8 0 0 1 5.1 16zm3-8h-3a8 8 0 0 1 4.3-3.6A15 15 0 0 0 8.1 8zM12 20c-.8-1.1-1.5-2.5-1.9-4h3.8c-.4 1.5-1.1 2.9-1.9 4zm2.3-6H9.7a14 14 0 0 1 0-4h4.6a14 14 0 0 1 0 4zm.3 5.6a15 15 0 0 0 1.3-3.6h3a8 8 0 0 1-4.3 3.6zm1.7-5.6a16 16 0 0 0 0-4h3.4a8 8 0 0 1 0 4z"/></svg>
        <span>www.hadleycarpentry.co.uk</span>
      </li>
    </ul>

    <div class="brand">
      <span class="brand__mark" aria-hidden="true"></span>
      <span class="brand__name">Tom Hadley Carpentry</span>
    </div>
  </section>

</body>
</html>
```